Exciting letterhead design for startup company

We need a A4 letterhead designing.

See attached file which contains the logo (on 3 different coloured backgrounds) and then the address and contact information. It also contains 4 colours that can be used.

Looking for an imaginative design. We are a young, fresh startup website design company so need a letterhead that reflects our industry.

Sans Serif

```html
<!DOCTYPE html>
<html lang="en">
<head>
<meta charset="utf-8">
<title>Pixelnest Letterhead</title>
<link href="https://fonts.googleapis.com/css2?family=Open+Sans:wght@400;600&display=swap" rel="stylesheet">
<style>
  :root {
    --backdrop: #e6e6e6;
    --paper: #ffffff;
    --brand-green: #5aaa55;
    --brand-blue: #0a86c9;
    --brand-yellow: #e2b203;
    --brand-dark: #38424c;
    --ink: #2b2b2b;
  }
  html, body {
    margin: 0;
    padding: 0;
    width: 1200px;
    height: 1006px;
    overflow: hidden;
    background: var(--backdrop);
    font-family: "Open Sans", Arial, sans-serif;
  }
  .letterhead {
    position: absolute;
    left: 282px;
    top: 53px;
    width: 636px;
    height: 900px;
    background: var(--paper);
    box-shadow: 0 2px 10px rgba(0, 0, 0, 0.08);
    overflow: hidden;
  }
  .letterhead__art {
    position: absolute;
    inset: 0;
    width: 100%;
    height: 100%;
  }
  .corner-decoration--top { fill: url(#corner-tone-top); }
  .corner-decoration--bottom { fill: url(#corner-tone-bottom); }
  .brand-tag {
    position: absolute;
    left: 48px;
    top: 112px;
    padding: 7px 16px;
    background: var(--brand-dark);
    color: #ffffff;
    font-weight: 600;
    font-size: 22px;
    line-height: 1;
    letter-spacing: -0.3px;
  }
  .footer-details {
    font-family: "Open Sans", Arial, sans-serif;
    font-size: 8.6px;
    fill: var(--ink);
  }
</style>
</head>
<body>
  <main class="letterhead">
    <svg class="letterhead__art" viewBox="0 0 636 900" xmlns="http://www.w3.org/2000/svg">
      <defs>
        <linearGradient id="corner-tone-top" x1="0" y1="0" x2="0.6" y2="1">
          <stop offset="0" stop-color="#7cb65a"/>
          <stop offset="1" stop-color="#d9b31c"/>
        </linearGradient>
        <linearGradient id="corner-tone-bottom" x1="1" y1="1" x2="0.4" y2="0">
          <stop offset="0" stop-color="#7cb65a"/>
          <stop offset="1" stop-color="#d9b31c"/>
        </linearGradient>
        <path id="footer-line-1" d="M20,904 Q495,860 640,713"/>
        <path id="footer-line-2" d="M60,914 Q510,876 646,730"/>
      </defs>
      <path class="corner-decoration--top" role="img" aria-label="Decorative corner sweep in brand green, blue and yellow" d="M0,0 H636 V24 Q150,60 0,250 Z"/>
      <path class="corner-decoration--bottom" role="img" aria-label="Decorative corner sweep in brand green, blue and yellow" d="M636,900 H0 V892 Q480,850 636,700 Z"/>
      <text class="footer-details">
        <textPath href="#footer-line-1" startOffset="95%" text-anchor="end">Suite 4, Harbour Court, Leeds LS1 4AB. Registered in England &amp; Wales | Company No. 09284615</textPath>
      </text>
      <text class="footer-details">
        <textPath href="#footer-line-2" startOffset="93%" text-anchor="end">0113 496 0827 | hello@pixelnest.co.uk | www.pixelnest.co.uk</textPath>
      </text>
    </svg>
    <div class="brand-tag">Pixelnest</div>
  </main>
</body>
</html>
```